Store Front Signage for an Upscale Cake & Dessert Bakery

We need a design for store front windows. We are a 12 year old bakery specializing in cakes, cupcakes, cookies, pies, and other desserts. We recently moved to a high traffic location.. and we would like to boost our visual presence; we can be seen from the main road but are competing with other businesses for attention. Attached is a photo of our store front with posters but this signage will be for window film for the entire window span. (see the store front to the left of the photo to see the green and yellow as a film example)
Our logo and store sign (not like in photo, that is showing more red) are in shades of pink. The most visible part of the signage is in the upper third to upper half of the 60" panels.
The signs in the window currently say Life's Short. Eat Cake.
We now use Enjoy Life. Eat Cake.
The design should span all the windows and door -- this can be individual panels or one design that covers all panels. I have pink and greys chosen but please DO NOT let this constrain you. The inside of the bakery has grey floors and walls. white cabinetry, black granite countertops. The only thing with color is the baked goods and display cakes, pictures of cakes, the logo and menu and employee shirts.

Target Market(s)

we are located at a busy intersection --- we would like to capture the attention of people in cars as they pass by and entice them to stop in

Font styles to use
Serif
Sans Serif

Colors
d3d3d3
757575
ffffff
e24197
e667a6
eea4c8
f9d9e8

Requirements
Must have
• I would like the design to be easily discernible at the road way that is about 75 feet from store front. If you look at the photos I provide, note that the font size that is easily readable from the road are the ones in the top panes (although the shadow from the building makes them difficult to see -- the best visibility is the top 1/3 of the 60" panels.
Nice to have
• would like to have some non-photo graphics of a cake ( like a birthday cake), tiered cake, cupcakes, and cookies or pie for the panels --- but DO NOT let this constrain you. I need something to grab attention while cars are stopped at the nearby traffic light.
• If this design works well... I will be changing the panel on a seasonal basis
Should not have
• words that cannot be read from a distance.

```html
<!DOCTYPE html>
<html lang="en">
<head>
<meta charset="utf-8">
<title>Marisol's Bake Shoppe – Storefront Window Film</title>
<link href="https://fonts.googleapis.com/css2?family=Lobster+Two:ital,wght@1,700&family=Josefin+Sans:wght@300;400;600;700&family=Oswald:wght@400;600&family=Open+Sans:ital,wght@0,400;0,700;1,700&display=swap" rel="stylesheet">
<style>
  :root{
    --page:#ebebeb;
    --frame:#1c1c1c;
    --teal-top:#3aaccb;
    --teal-bottom:#0f2a33;
    --berry:#951450;
    --blush:#eab4c8;
    --white:#ffffff;
    --hours-red:#e0201f;
  }
  *{margin:0;padding:0;box-sizing:border-box}
  html,body{width:1200px;height:1000px;overflow:hidden;background:var(--page)}
  .canvas{position:relative;width:1200px;height:1000px}
  .storefront{position:absolute;left:38px;top:224px;width:1124px;height:552px;background:var(--frame)}
  .pane{position:absolute;background:linear-gradient(180deg,var(--teal-top) 0%,var(--teal-bottom) 100%);overflow:hidden}
  .transom{top:9px;height:140px}
  .tall{top:159px;height:384px;background:none}
  .tall .upper{position:absolute;left:0;top:0;width:100%;height:245px;background:linear-gradient(180deg,var(--teal-top),var(--teal-bottom))}
  .tall .band-berry{position:absolute;left:0;top:245px;width:100%;height:36px;background:var(--berry)}
  .tall .band-gap{position:absolute;left:0;top:281px;width:100%;height:9px;background:var(--frame)}
  .tall .band-blush{position:absolute;left:0;top:290px;width:100%;height:13px;background:var(--blush)}
  .tall .band-white{position:absolute;left:0;top:305px;width:100%;height:4px;background:var(--white)}
  .tall .lower{position:absolute;left:0;top:309px;width:100%;height:75px;background:linear-gradient(180deg,#2c8ea8,var(--teal-bottom))}
  .col1{left:9px;width:225px}.col2{left:243px;width:225px}.col3{left:477px;width:169px}
  .col4{left:655px;width:225px}.col5{left:889px;width:225px}
  .slogan{position:absolute;top:20px;width:100%;text-align:center;font-family:"Lobster Two",cursive;font-style:italic;font-weight:700;font-size:76px;color:var(--white);line-height:1;
    text-shadow:3px 0 var(--berry),-3px 0 var(--berry),0 3px var(--berry),0 -3px var(--berry),2px 2px var(--berry),-2px -2px var(--berry),2px -2px var(--berry),-2px 2px var(--berry)}
  .door{position:absolute;left:479px;top:159px;width:167px;height:384px;background:#2a2a2a}
  .door-glass{position:absolute;left:12px;top:13px;width:142px;height:338px;background:linear-gradient(180deg,var(--teal-top),var(--teal-bottom))}
  .door-name{margin-top:46px;text-align:center;font-family:"Josefin Sans",sans-serif;font-weight:700;color:var(--berry);font-size:14px;line-height:1.1}
  .door-name small{display:block;font-weight:400;font-size:11px;color:var(--white)}
  .hours{text-align:center;font-family:"Open Sans",sans-serif;color:var(--white);font-size:7.5px;line-height:1.25;margin-top:6px}
  .hours h3{color:var(--hours-red);font-size:10px;font-weight:400;margin-bottom:2px}
  .hours p+p{margin-top:6px}

  .offer{position:absolute;left:0;top:0;width:100%;height:245px;color:var(--white);font-family:"Josefin Sans",sans-serif}
  .offer > div{position:absolute;left:0;width:100%;text-align:center;line-height:1;white-space:nowrap}
  .offer .custom{top:20px;font-weight:600;font-size:38px;letter-spacing:1px}
  .offer .cake{top:60px;font-weight:400;font-size:26px}
  .offer .holiday{top:84px;font-family:"Oswald",sans-serif;font-weight:600;font-size:36px}
  .offer .rule-top{top:124px;left:32px;width:161px;height:3px;background:var(--white)}
  .offer .desserts{top:130px;font-weight:300;font-size:25px;letter-spacing:4px;padding-left:4px}
  .offer .rule-mid{top:158px;left:40px;width:145px;height:2px;background:var(--white)}
  .offer .cupcakes{top:162px;font-family:"Oswald",sans-serif;font-weight:600;font-size:21px}
  .offer .cookies{top:188px;font-weight:400;font-size:17px;letter-spacing:2px;padding-left:2px}
  .offer .amp{top:205px;font-weight:700;font-size:13px}
  .offer .sweets{top:215px;font-family:"Lobster Two",cursive;font-style:italic;font-weight:700;font-size:22px}

  .brand{position:absolute;left:0;top:98px;width:100%;text-align:center;font-family:"Josefin Sans",sans-serif;font-weight:700;color:var(--white);font-size:21px;line-height:1.15}
  .brand-dot{display:block;width:30px;height:30px;border-radius:50%;background:var(--blush);margin:0 auto 10px}
  .service{position:absolute;left:0;top:36px;width:100%;text-align:center;color:var(--white);line-height:1}
  .service .next{font-family:"Josefin Sans",sans-serif;font-weight:700;font-size:26px}
  .service .pickup{font-family:"Josefin Sans",sans-serif;font-weight:400;font-size:38px}
  .service .avail{font-family:"Josefin Sans",sans-serif;font-weight:700;font-size:26px;margin-top:4px}
  .service .delivery{font-family:"Oswald",sans-serif;font-weight:600;font-size:28px;letter-spacing:1px}
  .service .order{display:inline-block;margin-top:12px;background:var(--white);color:#0f2a33;font-family:"Open Sans",sans-serif;font-style:italic;font-weight:700;font-size:17px;padding:2px 10px;width:153px}
  .service .web{font-family:"Open Sans",sans-serif;font-style:italic;font-weight:700;font-size:17px;margin-top:4px}
</style>
</head>
<body>
<div class="canvas">
  <div class="storefront">
    <div class="pane transom col1"><div class="slogan">enjoy</div></div>
    <div class="pane transom col2"><div class="slogan">life.</div></div>
    <div class="pane transom col3"></div>
    <div class="pane transom col4"><div class="slogan">eat</div></div>
    <div class="pane transom col5"><div class="slogan">cake.</div></div>

    <div class="pane tall col1">
      <div class="upper">
        <div class="offer">
          <div class="custom">Custom</div>
          <div class="cake">CAKE</div>
          <div class="holiday">HOLIDAY</div>
          <div class="rule-top"></div>
          <div class="desserts">DESSERTS</div>
          <div class="rule-mid"></div>
          <div class="cupcakes">CUPCAKES</div>
          <div class="cookies">·COOKIES·</div>
          <div class="amp">&amp;</div>
          <div class="sweets">sweets</div>
        </div>
      </div>
      <div class="band-berry"></div><div class="band-gap"></div><div class="band-blush"></div><div class="band-white"></div><div class="lower"></div>
    </div>

    <div class="pane tall col2">
      <div class="upper"><div class="brand"><span class="brand-dot"></span>MARISOL'S<br>BAKE SHOPPE</div></div>
      <div class="band-berry"></div><div class="band-gap"></div><div class="band-blush"></div><div class="band-white"></div><div class="lower"></div>
    </div>

    <div class="door">
      <div class="door-glass">
        <div class="door-name">MARISOL'S<small>· bake shoppe ·</small></div>
        <div class="hours">
          <h3>HOURS:</h3>
          <p>MONDAY-SATURDAY<br>09:00 AM - 02:00 PM</p>
          <p>SUNDAY<br>11:00 AM - 05:00 PM</p>
        </div>
      </div>
    </div>

    <div class="pane tall col4">
      <div class="upper"><div class="brand"><span class="brand-dot"></span>MARISOL'S<br>BAKE SHOPPE</div></div>
      <div class="band-berry"></div><div class="band-gap"></div><div class="band-blush"></div><div class="band-white"></div><div class="lower"></div>
    </div>

    <div class="pane tall col5">
      <div class="upper">
        <div class="service">
          <div class="next">NEXT DAY</div>
          <div class="pickup">PICK-UP</div>
          <div class="avail">AVAILABLE</div>
          <div class="delivery">DELIVERY</div>
          <div class="order">ORDER ONLINE</div>
          <div class="web">marisolbakes.com</div>
        </div>
      </div>
      <div class="band-berry"></div><div class="band-gap"></div><div class="band-blush"></div><div class="band-white"></div><div class="lower"></div>
    </div>
  </div>
</div>
</body>
</html>
```